Business Card Design

We like to use greens as you will see in our logo (but not TOO much green). We are a Dental Clinic in a somewhat eccentric community. We do not like the dated sharp designs which we see many dentists use. We're looking for something bright and fresh while still maintaining the integrity of the profession. Elegance is not necessarily what we are going for... we need for the design to be "mature" but also up-lifting.

See our logo.
Updates

Project Deadline Extended
Reason: We have 5 designs which we like. But we'd like to see a few more before committing to a design.

Project Deadline Extended
Reason: We are awaiting revisions to this project. We are still welcoming designs while we wait to see if designers are able to provide to us the revisions we require in order to proceed with a selection.

Target Market(s)

Younger families - ages late 20's to early 40's

Industry/Entity Type

Business

Contact Information for Business Card

Corwel T. Banfry DDS 2730 W. Halvert Rd. Ste. 7 Royal Oak, MI 48391 (248)555-0174 FX (248)555-0189 info@BrightwellDentalCareMi.com BrigthwellDentalCareMi.com on the back of the card we need an appointment reminder (For____ Date___ Time____) with "If you are unable to keep your appointment, kindly give 48 hours notice" at the bottom. No use of teeth in the design. DOUBLE SIDED DESIGN

Requirements
Should not have
• The use of pictures of teeth

```html
<!DOCTYPE html>
<html lang="en">
<head>
<meta charset="utf-8">
<title>Brightwell Dental Care – Business Card</title>
<link rel="stylesheet" href="https://fonts.googleapis.com/css2?family=Cinzel:wght@600&family=PT+Sans:ital,wght@0,400;0,700;1,400&display=swap">
<style>
  :root {
    --green-dark: #1d6a34;
    --green-mid: #2f8a3f;
    --green-light: #8cc63f;
    --ink: #2b2b2b;
    --ink-soft: #454545;
    --rule: #6d6d6d;
    --card: #ffffff;
    --backdrop: #ecebe7;
  }
  * { margin: 0; padding: 0; box-sizing: border-box; }
  html, body {
    width: 1200px; height: 1188px; overflow: hidden;
    background: var(--backdrop);
    font-family: "PT Sans", sans-serif;
    color: var(--ink);
  }
  .canvas { position: relative; width: 1200px; height: 1188px; }
  .card {
    position: absolute; width: 916px; height: 522px;
    background: var(--card);
    box-shadow: 0 2px 6px rgba(0,0,0,.18);
  }
  .card > * { position: absolute; }
  .card--front { left: 262px; top: 35px; }
  .card--back { left: 30px; top: 600px; }

  /* front */
  .brand { left: 115px; top: 60px; width: 400px; color: var(--green-dark); font-weight: 400; }
  .brand__mark {
    position: absolute; left: 186px; top: 0; width: 62px; height: 62px;
    border-radius: 50%; background: var(--green-light);
  }
  .brand__name { position: absolute; left: 0; top: 62px; font-size: 78px; line-height: 1; letter-spacing: -1px; }
  .brand__sub { position: absolute; left: 2px; top: 152px; font-size: 44px; line-height: 1; letter-spacing: 1px; }

  .contacts { left: 112px; top: 278px; list-style: none; font-size: 23px; }
  .contacts li { display: flex; align-items: center; height: 37px; }
  .contacts svg { width: 17px; height: 17px; margin-right: 9px; fill: var(--ink-soft); }

  .dentist { right: 28px; top: 280px; text-align: right; }
  .dentist__name { font-size: 31px; font-weight: 700; color: var(--green-dark); line-height: 1.2; }
  .dentist__title { font-size: 24px; color: var(--ink); line-height: 1.3; }

  .rule { top: 445px; height: 5px; }
  .rule--accent { left: 0; width: 87px; background: var(--green-light); }
  .rule--main { left: 93px; right: 0; background: var(--green-dark); }

  .address { left: 112px; top: 462px; font-size: 23px; }

  /* back */
  .appt__title {
    left: 0; right: 0; top: 92px; text-align: center;
    font-family: "Cinzel", serif; font-weight: 600; font-size: 35px;
    color: var(--green-dark); letter-spacing: .5px;
  }
  .field { font-size: 26px; color: var(--ink-soft); white-space: nowrap; }
  .dots { border-bottom: 2px dotted var(--rule); height: 2px; }
  .slot { border: 2px solid var(--rule); border-radius: 4px; height: 35px; }
  .day { font-size: 26px; font-weight: 700; color: var(--ink-soft); }
  .daybox { border: 2px solid var(--rule); border-radius: 4px; width: 56px; height: 35px; top: 372px; }
  .notice {
    left: 0; right: 0; top: 446px; text-align: center;
    font-style: italic; font-size: 25px; color: var(--ink);
  }
</style>
</head>
<body>
<main class="canvas">

  <section class="card card--front" aria-label="Card front">
    <div class="brand">
      <span class="brand__mark"></span>
      <span class="brand__name">Brightwell</span>
      <span class="brand__sub">DENTAL CARE</span>
    </div>

    <ul class="contacts">
      <li><svg viewBox="0 0 24 24"><path d="M6.6 10.8a15.1 15.1 0 0 0 6.6 6.6l2.2-2.2a1 1 0 0 1 1-.25 11.4 11.4 0 0 0 3.6.57 1 1 0 0 1 1 1V20a1 1 0 0 1-1 1A17 17 0 0 1 3 4a1 1 0 0 1 1-1h3.5a1 1 0 0 1 1 1c0 1.25.2 2.45.57 3.57a1 1 0 0 1-.25 1z"/></svg>(248)555-0174</li>
      <li><svg viewBox="0 0 24 24"><path d="M6 2h10l2 2v4H6zM4 9h16a2 2 0 0 1 2 2v6h-4v4H6v-4H2v-6a2 2 0 0 1 2-2zm4 7v3h8v-3z"/></svg>(248)555-0189</li>
      <li><svg viewBox="0 0 24 24"><path d="M2 5h20v14H2zm2 2v.5l8 5 8-5V7zm0 3v7h16v-7l-8 5z"/></svg>info@BrightwellDentalCareMi.com</li>
      <li><svg viewBox="0 0 24 24"><path d="M12 2a10 10 0 1 0 0 20 10 10 0 0 0 0-20zm6.9 6h-2.9a15 15 0 0 0-1.4-3.6A8 8 0 0 1 18.9 8zM12 4a13 13 0 0 1 1.9 4h-3.8A13 13 0 0 1 12 4zM4.3 14a8 8 0 0 1 0-4h3.4a16 16 0 0 0 0 4zm.8 2h2.9a15 15 0 0 0 1.4 3.6A8 8 0 0 1 5.1 16zM8 8H5.1a8 8 0 0 1 4.3-3.6A15 15 0 0 0 8 8zm4 12a13 13 0 0 1-1.9-4h3.8A13 13 0 0 1 12 20zm2.3-6H9.7a14 14 0 0 1 0-4h4.6a14 14 0 0 1 0 4zm.3 5.6A15 15 0 0 0 16 16h2.9a8 8 0 0 1-4.3 3.6zm1.7-5.6a16 16 0 0 0 0-4h3.4a8 8 0 0 1 0 4z"/></svg>BrigthwellDentalCareMi.com</li>
    </ul>

    <div class="dentist">
      <div class="dentist__name">Corwel T. Banfry</div>
      <div class="dentist__title">DDS</div>
    </div>

    <div class="rule rule--accent"></div>
    <div class="rule rule--main"></div>

    <p class="address">2730 W. Halvert Rd. Ste. 7 Royal Oak, MI 48391</p>
  </section>

  <section class="card card--back" aria-label="Appointment reminder">
    <h2 class="appt__title">YOUR APPOINTMENT</h2>

    <span class="field" style="left:72px;top:153px;">Name :</span>
    <div class="dots" style="left:173px;top:176px;width:667px;"></div>

    <span class="field" style="left:72px;top:218px;">Date :</span>
    <div class="dots" style="left:173px;top:241px;width:226px;"></div>
    <span class="field" style="left:411px;top:218px;">Time :</span>
    <div class="dots" style="left:491px;top:241px;width:245px;"></div>
    <span class="field" style="left:743px;top:218px;">am / pm</span>

    <span class="field" style="left:72px;top:283px;">Next Appointment</span>
    <div class="slot" style="left:325px;top:283px;width:166px;"></div>
    <div class="slot" style="left:503px;top:283px;width:166px;"></div>
    <div class="slot" style="left:678px;top:283px;width:166px;"></div>

    <span class="day" style="left:68px;top:373px;">MON</span>
    <div class="daybox" style="left:145px;"></div>
    <span class="day" style="left:211px;top:373px;">TUE</span>
    <div class="daybox" style="left:273px;"></div>
    <span class="day" style="left:341px;top:373px;">WED</span>
    <div class="daybox" style="left:414px;"></div>
    <span class="day" style="left:482px;top:373px;">THU</span>
    <div class="daybox" style="left:547px;"></div>
    <span class="day" style="left:615px;top:373px;">FRI</span>
    <div class="daybox" style="left:665px;"></div>
    <span class="day" style="left:733px;top:373px;">SAT</span>
    <div class="daybox" style="left:792px;"></div>

    <p class="notice">If you are unable to keep your appointment, kindly give 48 hours notice</p>
  </section>

</main>
</body>
</html>
```